RevelHubQZ Business Cards

Front
Has logo with a design. Website address (www.revelhubqz-example.net)
Has slogan (discover the nightlife)
Has phone number (5182297734)
Should be bold and stands out.

Back
Has details about what we offer.

Events
Search upcoming events
Submit events
Party Image Gallery
View and download HQ party images
Sign up as a contributing event photographer and get paid!
Tickets
Sell your event tickets online for free!
Direct pay
No ticket fee

Target Market(s)

These cards will be handed out in clubs and events to patrons.

Industry/Entity Type

Business

Contact Information for Business Card

Should match or mirror our website in some sort of way. Visit the website to get ideas.

Requirements
Must have
• Must be designed for a 3x3 inch card.

```html
<!DOCTYPE html>
<html lang="en">
<head>
<meta charset="utf-8">
<title>RevelHubQZ Business Cards</title>
<link rel="stylesheet" href="https://fonts.googleapis.com/css2?family=Ubuntu:wght@400;500&family=Arimo:wght@400;700&display=swap">
<style>
  :root {
    --stage: #3b3b3b;
    --card: #f6f6f6;
    --blue: #2f9fd3;
    --pink: #d63b8f;
    --white: #ffffff;
  }
  * { margin: 0; padding: 0; box-sizing: border-box; }
  html, body { width: 1200px; height: 750px; overflow: hidden; }
  body { background: var(--stage); position: relative; font-family: "Ubuntu", sans-serif; }
  .card {
    position: absolute;
    top: 233px;
    width: 286px;
    height: 286px;
    background: var(--card);
  }
  .card--front { left: 298px; }
  .card--back { left: 617px; }
  .brand {
    position: absolute;
    left: 0; right: 0;
    top: 36px;
    display: flex;
    flex-direction: column;
    align-items: center;
  }
  .brand__row { display: flex; align-items: center; gap: 8px; }
  .brand__dot { width: 26px; height: 26px; border-radius: 50%; background: var(--blue); }
  .brand__name { font-size: 24px; font-weight: 500; color: var(--blue); letter-spacing: -0.3px; }
  .brand__slogan {
    margin-top: 3px;
    font-size: 8px;
    letter-spacing: 3.4px;
    color: #555;
    padding-left: 32px;
  }
  .band {
    position: absolute;
    left: 0; right: 0;
    top: 142px;
    height: 113px;
    color: var(--white);
    text-align: center;
  }
  .band--blue { background: var(--blue); }
  .band--pink { background: var(--pink); }
  .phone {
    font-family: "Arimo", sans-serif;
    font-weight: 700;
    font-size: 37px;
    margin-top: 26px;
    line-height: 1;
    letter-spacing: 0.5px;
  }
  .website {
    font-family: "Arimo", sans-serif;
    font-weight: 700;
    font-size: 15px;
    margin-top: 5px;
  }
  .offer__title { font-size: 12px; margin-top: 22px; }
  .offer__list { list-style: none; margin-top: 5px; font-size: 8.4px; line-height: 11.2px; }
</style>
</head>
<body>
  <section class="card card--front">
    <div class="brand">
      <div class="brand__row">
        <span class="brand__dot"></span>
        <span class="brand__name">RevelHubQZ</span>
      </div>
      <span class="brand__slogan">discover the nightlife</span>
    </div>
    <div class="band band--blue">
      <p class="phone">5182297734</p>
      <p class="website">www.revelhubqz-example.net</p>
    </div>
  </section>

  <section class="card card--back">
    <div class="brand">
      <div class="brand__row">
        <span class="brand__dot"></span>
        <span class="brand__name">RevelHubQZ</span>
      </div>
      <span class="brand__slogan">discover the nightlife</span>
    </div>
    <div class="band band--pink">
      <h2 class="offer__title">Events</h2>
      <ul class="offer__list">
        <li>Search upcoming events ● Submit events</li>
        <li>Party Image Gallery ● View &amp; download HQ party images</li>
        <li>Sign up as a contributing event photographer &amp; get paid!</li>
        <li>Tickets ● Sell your event tickets online for free!</li>
        <li>Direct pay ● No ticket fee</li>
      </ul>
    </div>
  </section>
</body>
</html>
```